Business Card Design

We are a commercial real estate brokerage in San Francisco, leasing office buildings downtown.
I would like a clean, elegant look. Simple but powerful .

Industry/Entity Type

Business

Contact Information for Business Card

Derek Holloway
lic# 07258143
415.555.0172
derek@velt-commercial.example
velt-commercial.example

```html
<!DOCTYPE html>
<html lang="en">
<head>
<meta charset="utf-8">
<title>Velt Commercial – Business Card</title>
<link href="https://fonts.googleapis.com/css2?family=Source+Sans+3:ital,wght@0,400;0,600;1,400&display=swap" rel="stylesheet">
<style>
  :root {
    --page-bg: #9a9b9c;
    --card-bg: #e9e9ec;
    --brand-blue: #5d6e8e;
    --ink-dark: #3c3c3e;
    --ink-mid: #4a4a4d;
    --rule: #3a3a3c;
  }
  * { box-sizing: border-box; margin: 0; padding: 0; }
  html, body {
    width: 1105px;
    height: 1200px;
    overflow: hidden;
    background: var(--page-bg);
    font-family: "Source Sans 3", "Myriad Pro", Arial, sans-serif;
  }
  .card {
    position: absolute;
    left: 182px;
    width: 746px;
    height: 424px;
    background: var(--card-bg);
  }
  .card--front { top: 120px; }
  .card--back { top: 637px; }

  /* Front: brand lockup */
  .brand-lockup {
    position: absolute;
    left: 160px;
    top: 98px;
    height: 112px;
    display: flex;
    align-items: center;
  }
  .brand-mark {
    width: 56px;
    height: 56px;
    background: var(--ink-mid);
    margin-left: 64px;
  }
  .brand-divider {
    width: 2px;
    height: 112px;
    background: var(--rule);
    margin: 0 14px 0 28px;
  }
  .brand-name {
    font-weight: 600;
    color: var(--brand-blue);
    font-size: 48px;
    line-height: 1;
    letter-spacing: 0.5px;
  }

  /* Front: holder */
  .holder {
    position: absolute;
    right: calc(746px - 291px);
    top: 262px;
    text-align: right;
  }
  .holder__name {
    font-weight: 600;
    font-size: 27px;
    color: var(--brand-blue);
    line-height: 1.1;
  }
  .holder__licence {
    font-size: 19px;
    color: var(--ink-mid);
    margin-top: 4px;
  }

  /* Front: contact list */
  .contact-list {
    position: absolute;
    left: 325px;
    top: 250px;
    list-style: none;
  }
  .contact-list li {
    display: flex;
    align-items: center;
    height: 29px;
    font-size: 20px;
    color: var(--ink-dark);
  }
  .contact-list svg {
    width: 18px;
    height: 18px;
    margin-right: 10px;
    fill: var(--brand-blue);
    flex: none;
  }

  /* Back */
  .back-brand {
    position: absolute;
    left: 0;
    right: 0;
    top: 150px;
    text-align: center;
    font-weight: 600;
    font-size: 56px;
    color: var(--brand-blue);
    letter-spacing: 0.5px;
  }
  .tagline {
    position: absolute;
    left: 0;
    right: 0;
    top: 316px;
    text-align: center;
    font-style: italic;
    font-size: 19px;
    line-height: 28px;
    color: var(--ink-mid);
  }
</style>
</head>
<body>
  <section class="card card--front">
    <div class="brand-lockup">
      <div class="brand-mark"></div>
      <div class="brand-divider"></div>
      <div class="brand-name">Velt Commercial</div>
    </div>

    <div class="holder">
      <p class="holder__name">Derek Holloway</p>
      <p class="holder__licence">lic# 07258143</p>
    </div>

    <ul class="contact-list">
      <li>
        <svg viewBox="0 0 24 24" aria-hidden="true"><path d="M6.6 10.8a15.1 15.1 0 0 0 6.6 6.6l2.2-2.2c.3-.3.7-.4 1-.2 1.1.4 2.3.6 3.6.6.6 0 1 .4 1 1V20c0 .6-.4 1-1 1A17 17 0 0 1 3 4c0-.6.4-1 1-1h3.5c.6 0 1 .4 1 1 0 1.3.2 2.5.6 3.6.1.3 0 .7-.2 1z"/></svg>
        415.555.0172
      </li>
      <li>
        <svg viewBox="0 0 24 24" aria-hidden="true"><path d="M2 5h20v14H2zm2 2v.5l8 5 8-5V7l-8 5z"/></svg>
        derek@velt-commercial.example
      </li>
      <li>
        <svg viewBox="0 0 24 24" aria-hidden="true"><path d="M12 2a10 10 0 1 0 0 20 10 10 0 0 0 0-20zm-1 17.9A8 8 0 0 1 4.1 9.8L9 14.6v1a2 2 0 0 0 2 2zm6.9-2.5A2 2 0 0 0 16 16h-1v-3a1 1 0 0 0-1-1H8v-2h2a1 1 0 0 0 1-1V7h2a2 2 0 0 0 2-2v-.4a8 8 0 0 1 2.9 12.8z"/></svg>
        velt-commercial.example
      </li>
    </ul>
  </section>

  <section class="card card--back">
    <div class="back-brand">Velt Commercial</div>
    <p class="tagline">commercial real estate brokerage in San Francisco<br>leasing office buildings downtown.</p>
  </section>
</body>
</html>
```